Personal Training Business at home (Fern Vitality & Health)

My business name will be Fern Vitality & Health and will be training people with special needs (Asthma, Diabetes, Obesity, Rehab, Sports Performance) for all ages. It will be set indoor and outdoor for all types of weather conditions. I,m also doing Pilates group classes as well in a Japanese garden setting.I will be working alone so the groups will be small and the client has a high quality of service. I just need something very basic to start with then as the business expands I can edit it to it,s growth.

Target Market(s)

Target special population persons with dysfunctions injuries, metabolic/cardio-respiratory conditions, sports performance and more also healthy food choices.

Industry/Entity Type

Business

Number of Pages Required

3 page

Font styles to use
Serif

Colors
f78f20
ffffff
474747
cbcbcb
abd036

Requirements
Must have
• The website must have accessibility for change, to be able to link on other networks like my own YouTube videos. A basic lay out so I can fill in the pages and ad more as I expand the business. The logo to have the A for Fern to be an image of a man shaped as the letter A with his arms extended out/up. Private Facility and must ring for appointment to enter premises.
Nice to have
• The Image I want to have in my studio is for people to be serious about training & health choices. I want them to be able to train in a comfortable environment and free of air conditioned concrete rooms with machines. My home is converted to a Organic feature and outdoor/indoor training facility that my clients & I can share the natural freedom of training in the elements. My client have special needs and need extra care, they are people with injuries, metabolic/cardio-respiratory condition, asthmatics & more they need to be screened and tested for the condition that they suffer from and together with there allied professional we work together to treat them with the up most care for maximum results. This is what I want to target I long term client with real Goals on there mind and not some pipe dream.
Should not have
• Not to be portray as a Gym with machines and clients that only care about image.

```html
<!DOCTYPE html>
<html lang="en">
<head>
<meta charset="utf-8">
<title>Fern Vitality &amp; Health</title>
<link href="https://fonts.googleapis.com/css2?family=Open+Sans:wght@400;600;700&family=Oswald:wght@400;500&display=swap" rel="stylesheet">
<style>
:root{
  --orange:#f78f20;
  --white:#ffffff;
  --ink:#474747;
  --grey:#cbcbcb;
  --lime:#abd036;
  --lime-deep:#8ab82b;
  --footer-green:#7ca51c;
  --dark:#1c1c1c;
  --paper:#f2f2f2;
  --body:'Open Sans',Arial,sans-serif;
  --display:'Oswald','Arial Narrow',sans-serif;
}
*{box-sizing:border-box;margin:0;padding:0}
html,body{width:1200px;height:2647px;overflow:hidden}
body{font-family:var(--body);color:var(--ink);background:var(--white);position:relative}
a{color:inherit;text-decoration:none}

/* header */
.site-header{position:absolute;top:0;left:0;width:1200px;height:118px;background:var(--white);box-shadow:0 2px 6px rgba(0,0,0,.06)}
.brand{position:absolute;left:88px;top:44px;display:flex;align-items:center;gap:10px}
.brand-mark{width:22px;height:22px;background:var(--ink)}
.brand-name{font-family:var(--display);font-weight:500;font-size:27px;color:var(--lime-deep);letter-spacing:.3px}
.main-nav{position:absolute;top:56px;left:0;width:1200px;font-size:13px;font-weight:600;color:var(--ink)}
.main-nav a{position:absolute;white-space:nowrap}
.main-nav a.active{color:var(--orange)}
.search-box{position:absolute;left:1077px;top:46px;width:38px;height:36px;border:1px solid #e3e3e3}

/* hero */
.hero{position:absolute;top:118px;left:0;width:1200px;height:593px;background:radial-gradient(ellipse at 60% 40%,#9fcf4d 0%,#5f9a24 45%,#2f5a12 100%)}
.hero-photo{position:absolute;inset:0;background:linear-gradient(180deg,rgba(255,255,255,.06),rgba(0,0,0,.08) 70%,#6f9b2a 92%,#5d8a1f 100%)}
.hero-title{position:absolute;left:85px;top:248px;font-family:var(--display);font-size:58px;font-weight:400;color:var(--white);letter-spacing:.5px;line-height:1}
.hero-sub{position:absolute;left:85px;top:318px;font-family:var(--display);font-size:29px;color:var(--white);line-height:1}
.hero-arrows{position:absolute;left:85px;top:377px;display:flex;gap:10px}
.hero-arrows span{width:35px;height:35px;border-radius:50%;background:rgba(0,0,0,.35);display:flex;align-items:center;justify-content:center}

/* welcome */
.welcome{position:absolute;top:711px;left:0;width:1200px;height:203px;background:var(--white);text-align:center}
.section-title{font-size:22px;font-weight:600;color:var(--dark);text-transform:uppercase;letter-spacing:.3px}
.section-title em{font-style:normal;color:var(--orange)}
.welcome .section-title{margin-top:52px}
.welcome p{width:1016px;margin:14px auto 0;text-align:left;font-size:12.5px;line-height:23px;color:#666;height:70px;overflow:hidden}

/* training services */
.services{position:absolute;top:914px;left:0;width:1200px;height:427px;background:linear-gradient(135deg,#a7cf3a 0%,#9ac431 50%,#a9d13b 100%)}
.services .section-title{position:absolute;top:48px;width:100%;text-align:center;color:var(--white);font-size:23px}
.services .lead{position:absolute;top:88px;width:100%;text-align:center;color:var(--white);font-size:15px}
.service-card{position:absolute;top:145px;width:238px;height:231px;background:var(--white);padding:4px}
.service-photo{height:181px;width:100%}
.service-card h3{font-size:14px;font-weight:400;color:#111;text-align:center;margin-top:14px}

/* why train */
.why{position:absolute;top:1341px;left:0;width:1200px;height:412px;background:var(--white)}
.video-frame{position:absolute;left:88px;top:62px;width:491px;height:295px;border:1px solid #cfcfcf;box-shadow:0 1px 4px rgba(0,0,0,.25);padding:12px;background:var(--white)}
.video-still{position:relative;width:100%;height:100%;background:linear-gradient(120deg,#4e6a2e 0%,#7a5a3c 45%,#a06d44 70%,#b98a62 100%);border-radius:3px;overflow:hidden}
.video-play{position:absolute;left:205px;top:95px;width:56px;height:56px;border-radius:50%;background:rgba(40,40,40,.8)}
.video-bar{position:absolute;left:0;bottom:0;width:100%;height:38px;background:#1a1a1a;font-size:11px;color:#ddd}
.why-copy{position:absolute;left:604px;top:70px;width:508px}
.why-copy .section-title{font-size:20px}
.why-copy p{font-size:12.5px;line-height:25px;color:#555;margin-top:18px}
.btn{position:absolute;left:604px;top:307px;width:134px;height:39px;background:linear-gradient(180deg,#a9d13c,#86b425);color:var(--white);font-size:15px;display:flex;align-items:center;justify-content:center;border-radius:2px}

/* trading hours */
.hours{position:absolute;top:1753px;left:0;width:1200px;height:321px;background:linear-gradient(180deg,#2b3a22 0%,#1d2818 55%,#334a25 100%)}
.hours .section-title{position:absolute;top:42px;width:100%;text-align:center;color:var(--white);font-size:23px}
.hours-card{position:absolute;top:97px;width:500px;height:173px;background:var(--orange);color:var(--white);padding:26px 40px}
.hours-card h3{font-size:19px;font-weight:600;margin-bottom:8px}
.hours-card p{font-size:15.5px;font-weight:600;line-height:31px}

/* blog */
.blog{position:absolute;top:2074px;left:0;width:1200px;height:286px;background:var(--paper)}
.blog .section-title{position:absolute;left:92px;top:38px;font-size:18px}
.blog .section-title em{color:#1c6fae}
.blog-arrows{position:absolute;left:1088px;top:40px;font-size:18px;color:var(--dark);font-weight:700;letter-spacing:2px}
.blog-post{position:absolute;top:88px;width:480px;height:146px}
.blog-thumb{position:absolute;left:0;top:0;width:212px;height:146px;border:3px solid var(--white);box-shadow:0 1px 3px rgba(0,0,0,.3)}
.blog-text{position:absolute;left:228px;top:6px;width:252px}
.blog-text h3{font-size:13px;font-weight:600;color:var(--dark)}
.blog-text time{display:block;font-size:10px;color:var(--orange);margin-top:5px}
.blog-text p{font-size:9.5px;line-height:17px;color:#777;margin-top:6px}
.blog-text a{display:block;font-size:10.5px;color:var(--orange);margin-top:10px}

/* footer */
.site-footer{position:absolute;top:2360px;left:0;width:1200px;height:220px;background:var(--footer-green);color:var(--white)}
.footer-col{position:absolute;top:50px}
.footer-col h4{font-size:14.5px;font-weight:400;text-transform:uppercase;letter-spacing:.3px;margin-bottom:16px}
.footer-col p{font-size:12px;line-height:22px}
.newsletter input{display:block;width:214px;height:31px;border:1px solid #ccc;margin-top:12px;padding:0 10px;font-family:var(--body);font-size:12px;color:#555}
.newsletter button{margin-top:12px;width:94px;height:30px;background:#333;color:var(--white);border:0;border-radius:3px;font-family:var(--body);font-size:11px}
.social li{list-style:none;display:flex;align-items:center;gap:16px;font-size:12.5px;height:43px}
.social li span{width:34px;height:34px;border:2px solid rgba(255,255,255,.85);border-radius:50%}
.copyright{position:absolute;top:2580px;left:0;width:1200px;height:67px;background:#111;color:var(--white);font-size:11.5px;display:flex;align-items:center;justify-content:center}
</style>
</head>
<body>

<header class="site-header">
  <a class="brand" href="#"><span class="brand-mark"></span><span class="brand-name">FERN VITALITY &amp; HEALTH</span></a>
  <nav class="main-nav">
    <a class="active" style="left:476px">HOME</a>
    <a style="left:545px">ABOUT US</a>
    <a style="left:641px">TRAINING SERVICES</a>
    <a style="left:798px">TRADING HOURS</a>
    <a style="left:934px">BLOG</a>
    <a style="left:999px">CONTACTS</a>
  </nav>
  <div class="search-box">
    <svg width="38" height="36" viewBox="0 0 38 36"><circle cx="18" cy="17" r="4.5" fill="none" stroke="#666" stroke-width="1.5"/><line x1="21.3" y1="20.3" x2="24" y2="23" stroke="#666" stroke-width="1.5"/></svg>
  </div>
</header>

<section class="hero">
  <div class="hero-photo" role="img" aria-label="Two people stretching outdoors on grass in a sunny green park"></div>
  <h1 class="hero-title">FERN FITNESS</h1>
  <p class="hero-sub">personal training &amp; fitness</p>
  <div class="hero-arrows">
    <span><svg width="12" height="14" viewBox="0 0 12 14"><polyline points="8,2 3,7 8,12" fill="none" stroke="#fff" stroke-width="2"/></svg></span>
    <span><svg width="12" height="14" viewBox="0 0 12 14"><polyline points="4,2 9,7 4,12" fill="none" stroke="#fff" stroke-width="2"/></svg></span>
  </div>
</section>

<section class="welcome">
  <h2 class="section-title">Welcome to <em>Fern Fitness</em></h2>
  <p>FERNFIT has trainers that have a Diploma of fitness from the Wattle Institute &amp; are trained and qualified with the latest training techniques available anywhere in Australia, to give clients a better &amp; more reliable service with cutting edge training programs and testing. The foundation of this business will be to service clients by functional training techniques and some machines, with a combination of group classes &amp; one on one Personal training. We also have an area for Pilates experience this is a very Japanese influenced garden.</p>
</section>

<section class="services">
  <h2 class="section-title">Training Services</h2>
  <p class="lead">Lorem Ipsum is simply dummy text of the printing and typesetting industry</p>
  <article class="service-card" style="left:92px">
    <div class="service-photo" role="img" aria-label="Trainer and client stretching together on a lawn" style="background:linear-gradient(160deg,#6f9a3c,#a8c46a 60%,#d8849a)"></div>
    <h3>Personal training one on one</h3>
  </article>
  <article class="service-card" style="left:355px">
    <div class="service-photo" role="img" aria-label="Woman seated in a meditation pose outdoors" style="background:linear-gradient(160deg,#5c8a3a,#9bbb6c 55%,#e6e2dc)"></div>
    <h3>Group functional training</h3>
  </article>
  <article class="service-card" style="left:618px">
    <div class="service-photo" role="img" aria-label="Woman doing a stretch on a blue mat on grass" style="background:linear-gradient(170deg,#4f7f2c,#6fa33a 55%,#3ab0c8)"></div>
    <h3>Sports performance</h3>
  </article>
  <article class="service-card" style="left:874px">
    <div class="service-photo" role="img" aria-label="Woman stretching on grass in a park" style="background:linear-gradient(170deg,#7aa24a,#b7c98a 50%,#6f9a34)"></div>
    <h3>Recovery &amp; stretching classes</h3>
  </article>
</section>

<section class="why">
  <div class="video-frame">
    <div class="video-still" role="img" aria-label="Video still of a timber deck garden training area">
      <span class="video-play"><svg width="56" height="56" viewBox="0 0 56 56"><polygon points="22,17 40,28 22,39" fill="#fff"/></svg></span>
      <div class="video-bar">
        <svg width="467" height="38" viewBox="0 0 467 38">
          <circle cx="20" cy="19" r="6" fill="none" stroke="#ddd" stroke-width="1.5"/>
          <polygon points="18,16 23,19 18,22" fill="#ddd"/>
          <rect x="38" y="15" width="8" height="8" fill="#c0392b"/>
          <rect x="50" y="17" width="20" height="4" fill="#555"/>
          <rect x="76" y="18" width="110" height="2" fill="#c0392b"/>
          <rect x="186" y="18" width="80" height="2" fill="#555"/>
          <text x="357" y="23" font-family="Open Sans, sans-serif" font-size="11" fill="#ddd">01:30 / 04:55</text>
          <rect x="420" y="14" width="12" height="9" fill="none" stroke="#ddd" stroke-width="1.2"/>
          <circle cx="448" cy="19" r="5" fill="none" stroke="#ddd" stroke-width="2"/>
        </svg>
      </div>
    </div>
  </div>
  <div class="why-copy">
    <h2 class="section-title">Why train <em>with us</em></h2>
    <p>Our training services covers a wide variety of clients from different walks of life, like builders, plumbers, electricians, mechanics, truck drivers to your everyday common office workers, teachers, taxi drivers, nurses &amp; doctors and more.</p>
    <p>All these people are all eligible for this type of training. It is a great way to restore functional movement to deal with the everyday demands of your body &amp; just general fitness, health &amp; wellbeing.</p>
  </div>
  <a class="btn" href="#">Read More</a>
</section>

<section class="hours" role="img" aria-label="Dim background photo of people exercising on grass">
  <h2 class="section-title">Trading Hours</h2>
  <div class="hours-card" style="left:88px">
    <h3>APRIL - SEPTEMBER</h3>
    <p>Monday – Friday 4.00pm - 6.00pm (Finish by 7:00pm )</p>
    <p>Saturday- 12:00pm – 5:00pm &nbsp;(Finish by 6:00pm)</p>
    <p>Sunday - 6:00am – 11:00am(Finish by 12:00pm)</p>
  </div>
  <div class="hours-card" style="left:609px">
    <h3>OCTOBER – MARCH</h3>
    <p>Monday – Friday 6:00am – 7:00pm (Finish by 8:00pm)</p>
    <p>Saturday – 12:00pm – 5:00pm &nbsp;(Finish by 6:00pm)</p>
    <p>Sunday- 6:00am – 11:00am (Finish by 12:00pm)</p>
  </div>
</section>

<section class="blog">
  <h2 class="section-title">Latest <em>Blog</em></h2>
  <div class="blog-arrows">&lsaquo;&rsaquo;</div>
  <article class="blog-post" style="left:90px">
    <div class="blog-thumb" role="img" aria-label="Garden planter boxes on a timber deck" style="background:linear-gradient(150deg,#4c6b2e,#8a5a3a 60%,#c96b2a)"></div>
    <div class="blog-text">
      <h3>SIMPLY DUMMY TEXT</h3>
      <time>21-sep-2015</time>
      <p>Lorem Ipsum has been the industry's standard dummy text ever since the 1500s, when an unknown printer took a galley of type and scrambled it to make a type specimen book. It has survived not only five centuries, but also popularised</p>
      <a href="#">Read More &gt;&gt;</a>
    </div>
  </article>
  <article class="blog-post" style="left:618px">
    <div class="blog-thumb" role="img" aria-label="Group of people doing push-ups outdoors" style="background:linear-gradient(150deg,#7fae4a,#b9c98e 50%,#c59a78)"></div>
    <div class="blog-text">
      <h3>SIMPLY DUMMY TEXT</h3>
      <time>21-sep-2015</time>
      <p>Lorem Ipsum has been the industry's standard dummy text ever since the 1500s, when an unknown printer took a galley of type and scrambled it to make a type specimen book. It has survived not only five centuries, but also popularised</p>
      <a href="#">Read More &gt;&gt;</a>
    </div>
  </article>
</section>

<footer class="site-footer">
  <div class="footer-col newsletter" style="left:86px">
    <h4>Newsletters Sign Up</h4>
    <p>Sign up for our daily email by entering<br>your information below</p>
    <input type="text" value="Email address" aria-label="Email address">
    <button type="button">SUBSCRIBE</button>
  </div>
  <div class="footer-col" style="left:385px;width:230px">
    <h4>Group Training Section</h4>
    <p style="padding-left:4px">This area can accommodate 4-6 people at a time comfortably with a beautiful surrounding of a Japanese influenced garden. We have a combination of equipment like Kettle Bells, Dumbbells</p>
  </div>
  <div class="footer-col" style="left:699px">
    <h4>Get In Touch</h4>
    <p style="padding-left:4px">Address : 58 Kelpie Lane,<br>Mossvale, NSW<br>Phone : 02 5550 1874<br>Email : hello@fernvitality.example</p>
  </div>
  <div class="footer-col" style="left:960px">
    <h4>Follow Us On</h4>
    <ul class="social">
      <li><span></span>Friendpage</li>
      <li><span></span>Chirpline</li>
      <li><span></span>Snapgrove</li>
    </ul>
  </div>
</footer>

<div class="copyright">Copyright © 2016 &nbsp;All Rights Reserved</div>

</body>
</html>
```